Meal Plan Website Needs New Pages Designed

Brightwick Supper Kits is an online, membership based program that delivers weekly meal programs (7 days worth of recipes plus shopping lists) carefully crafted by an expert team of meal planners. All recipes are created to comply with the following macronutrient ratio: 65% healthy fats, 25% lean protein, 10% good carbs.
All recipes are Paleo friendly and a great resource for those individuals who want to correctly implement this type of diet.

We are re-designing our website and need the following pages designed:

· Home page w/ logo
· How it works page
· Get Started! page
· Recipes Page template (these will be the pages on our site that will have recipes)
· Kitchen Essentials Training page (this will be a page with videos and tips + tricks, PDFs, etc)

So 5 total PSDs, 1 for each page.

Target audience: Men and women between the ages of 30 and 60 who want to:
· Eat healthy
· Lose weight
· Follow/Implement the Paleo diet
· Take the guesswork out of preparing delicious AND healthy meals for them and their families
· Know exactly what to eat, what to buy, how to make it

Feelings/Messages we want to communicate through the design:
· “Organic” but elegant look
· Fresh/light/Airy
· Simple but NOT GENERIC
· “I want to get cooking” feeling

Our Stylistic preferences:
· Minimalist with a few bold elements (something in between)
· Easy to visually navigate (enough white space, but not too much)
· There is more to “see” than to “read”

Our Color Preferences:
· Lighter pallet
· Colors that evoke natural woods, granite countertops…
· Stay away from using all dark colors

Our Font Type Preferences:
· Easy to read
· Not more than 3 font types
· Not too rigid
· Not too sophisticated
· Simple with a touch

Examples of Website Designs that we like:
· http://www.dorvanta.com/meal-plans/
· http://grulvix.com/
· https://www.mistobarn.com/

```html
<!DOCTYPE html>
<html lang="en">
<head>
<meta charset="utf-8">
<title>Brightwick Supper Kits</title>
<link rel="stylesheet" href="https://fonts.googleapis.com/css2?family=Open+Sans:wght@400;600;700&display=swap">
<style>
:root{
  --orange:#fdb94a;
  --red:#ec2228;
  --brown:#5a2a12;
  --text:#444;
  --wood-a:#e9cfa6;
  --wood-b:#dcb987;
  --gray:#f1f1f1;
  --line:#e2e2e2;
  --white:#fff;
}
*{box-sizing:border-box;margin:0;padding:0}
html,body{width:1200px;height:2671px;overflow:hidden}
body{position:relative;font-family:"Open Sans",Arial,sans-serif;color:var(--text);background:var(--white)}
.abs{position:absolute}
.wood{background:linear-gradient(90deg,var(--wood-a),var(--wood-b) 20%,var(--wood-a) 40%,var(--wood-b) 60%,var(--wood-a) 80%,var(--wood-b))}

/* header */
.header{left:0;top:0;width:1200px;height:124px}
.brand{left:0;top:62px;width:1200px;display:flex;justify-content:center;align-items:center;gap:12px}
.brand-dot{width:26px;height:26px;border-radius:50%;background:var(--red)}
.brand-name{font-size:26px;font-weight:600;color:var(--red);letter-spacing:.5px}
.ribbon{top:0;width:66px;height:68px;color:var(--white);font-size:13px;font-weight:600;text-align:center;line-height:16px;padding-top:14px;clip-path:polygon(0 0,100% 0,100% 100%,50% 82%,0 100%)}
.ribbon.sign{left:981px;background:var(--red)}
.ribbon.join{left:1059px;background:var(--orange)}
.search{left:885px;top:84px;width:240px;height:30px;background:var(--white);border:1px solid #ccc;border-radius:3px;font-size:11px;font-style:italic;color:#999;padding:7px 10px}
.search svg{position:absolute;right:8px;top:6px}

.nav{left:0;top:124px;width:1200px;height:77px;background:var(--orange);display:flex;justify-content:space-between;align-items:center;padding:0 73px}
.nav a{font-size:12.5px;font-weight:600;color:var(--brown);text-decoration:none;text-transform:uppercase}

/* hero */
.hero{left:0;top:201px;width:1200px;height:440px;background:var(--white)}
.hero-photo{left:427px;top:0;width:773px;height:440px;background:linear-gradient(90deg,#fff 0%,#e8eef0 10%,#9fbf6a 35%,#f29a6a 55%,#7fa84b 70%,#3e4a45 100%)}
.hero-copy{left:73px;top:82px}
.hero-copy .pre{font-size:30px;color:#333;letter-spacing:.5px}
.hero-copy h1{font-size:38px;font-weight:400;color:var(--red);letter-spacing:.5px;margin-top:-2px}
.hero-copy p{font-size:24px;color:#555;line-height:30px;margin-top:8px;width:420px}
.btn{display:inline-block;color:var(--white);font-weight:600;text-transform:uppercase;text-align:center}
.btn-red{background:var(--red)}
.btn-orange{background:var(--orange)}
.hero-btn{left:73px;top:258px;width:329px;height:50px;line-height:50px;font-size:17px}
.dots{left:73px;top:394px;display:flex;gap:9px}
.dots span{width:15px;height:15px;border-radius:50%;background:#999}
.dots span:first-child{background:#222}

/* sections */
.band{left:0;width:1200px;background:var(--gray);border-bottom:1px solid var(--line)}
.section-title{left:0;width:1200px;text-align:center;font-size:24px;font-weight:600;color:var(--brown);text-transform:uppercase}

.step{top:733px;width:331px;height:347px;background:var(--orange);text-align:center;box-shadow:0 1px 3px rgba(0,0,0,.12)}
.step h3{margin-top:30px;font-size:21px;font-weight:600;color:var(--brown);text-transform:uppercase}
.step .icon{width:120px;height:120px;margin:20px auto 0;border-radius:50%;background:var(--white);display:flex;align-items:center;justify-content:center}
.step p{font-size:12.5px;line-height:21px;color:#333;margin:28px 35px 0}
.step .btn{width:151px;height:46px;line-height:46px;font-size:12px;margin-top:33px}

.why p{left:90px;top:1180px;width:1020px;font-size:12.5px;line-height:21.5px;text-align:center;color:#555}
.why-btn{left:506px;top:1314px;width:194px;height:48px;line-height:48px;font-size:14px}

.recipe{width:513px;height:206px;background:var(--white);border:1px solid var(--line);box-shadow:0 1px 4px rgba(0,0,0,.08)}
.recipe .dish{position:absolute;left:22px;top:25px;width:156px;height:156px;border-radius:50%;border:4px solid #eee}
.recipe h4{position:absolute;left:193px;top:22px;font-size:20px;font-weight:400;color:#222}
.recipe p{position:absolute;left:193px;top:56px;width:300px;font-size:12.5px;line-height:19px;color:#555}
.recipe .btn{position:absolute;top:145px;width:109px;height:38px;line-height:38px;font-size:11px}
.recipe .more{left:193px}
.recipe .join{left:320px}
.d1{background:radial-gradient(circle,#7da74a,#3f6b2b)}
.d2{background:radial-gradient(circle,#f2a33a,#6d9a3e)}
.d3{background:radial-gradient(circle,#e9876a,#8fb25a)}
.d4{background:radial-gradient(circle,#e9c14c,#5c7a3a)}

.expert{left:73px;width:1054px;height:165px;background:var(--white);border:1px solid var(--line);box-shadow:0 1px 4px rgba(0,0,0,.08)}
.expert .portrait{position:absolute;top:12px;width:140px;height:140px;border-radius:50%;border:4px solid #eee}
.expert h4{position:absolute;top:26px;font-size:20px;font-weight:600;color:var(--red)}
.expert .role{position:absolute;top:53px;font-size:14px;color:var(--orange)}
.expert p{position:absolute;top:74px;width:870px;font-size:12.5px;line-height:21.5px;color:#555}
.expert.left .portrait{left:13px;background:linear-gradient(160deg,#d7b59a,#9c8270)}
.expert.left h4,.expert.left .role,.expert.left p{left:182px}
.expert.right .portrait{right:13px;background:linear-gradient(160deg,#c8c9cc,#7c7f86)}
.expert.right h4,.expert.right .role,.expert.right p{right:182px;text-align:right}

/* footer */
.footer{left:0;top:2405px;width:1200px;height:215px}
.footer h5{position:absolute;top:30px;font-size:16px;font-weight:600;color:var(--brown);text-transform:uppercase}
.footer .about{position:absolute;left:73px;top:58px;width:300px;font-size:12.5px;line-height:21px;color:#3a2a1a}
.links{position:absolute;top:60px;list-style:none;font-size:12.5px;line-height:27.5px;color:#3a2a1a}
.social{position:absolute;left:650px;top:64px;display:flex;gap:11px}
.social span{width:25px;height:25px;background:var(--brown);opacity:.8}
.field{position:absolute;left:885px;width:240px;height:32px;background:var(--white);border:1px solid #ddd;font-size:12px;color:#999;padding:7px 14px}
.submit{position:absolute;left:1036px;top:142px;width:89px;height:32px;line-height:32px;font-size:12px}
.copy{left:0;top:2620px;width:1200px;height:51px;background:var(--orange);text-align:center;line-height:51px;font-size:11.5px;color:var(--brown)}
</style>
</head>
<body>

<header class="abs header wood">
  <div class="abs brand"><span class="brand-dot"></span><span class="brand-name">BRIGHTWICK SUPPER KITS</span></div>
  <a class="abs ribbon sign">SIGN<br>IN</a>
  <a class="abs ribbon join">JOIN<br>NOW</a>
  <div class="abs search">Search...
    <svg width="18" height="18" viewBox="0 0 18 18"><circle cx="7" cy="7" r="5" fill="none" stroke="#ec2228" stroke-width="2"/><line x1="11" y1="11" x2="16" y2="16" stroke="#ec2228" stroke-width="2.5"/></svg>
  </div>
</header>

<nav class="abs nav">
  <a>Home</a><a>Recipes</a><a>Meal Plans</a><a>How it Works</a><a>Resources</a><a>Our Experts</a><a>Success Stories</a><a>Blog</a><a>Contact Us</a>
</nav>

<section class="abs hero">
  <div class="abs hero-photo" role="img" aria-label="Plated salmon fillet with green salad, onion rings, carrot and cherry tomatoes"></div>
  <div class="abs hero-copy">
    <div class="pre">WELCOME TO</div>
    <h1>BRIGHTWICK SUPPER KITS</h1>
    <p>Carefully Crafted by an Expert Team of Meal Planners.</p>
  </div>
  <a class="abs btn btn-red hero-btn">More about Brightwick Supper Kits</a>
  <div class="abs dots"><span></span><span></span><span></span><span></span></div>
</section>

<div class="abs band" style="top:641px;height:128px"></div>
<h2 class="abs section-title" style="top:668px">How it Works</h2>

<article class="abs step" style="left:73px">
  <h3>Meal Plans</h3>
  <div class="icon"><svg width="66" height="56" viewBox="0 0 66 56"><path d="M24 4c-4 4 4 6 0 10M33 2c-4 4 4 6 0 10M42 4c-4 4 4 6 0 10" fill="none" stroke="#ec2228" stroke-width="3"/><path d="M3 22h60c0 14-12 24-30 24S3 36 3 22z" fill="#ec2228"/><path d="M22 48h22v6H22z" fill="#ec2228"/></svg></div>
  <p>Aliquam molestie, mi et imperdiet euismod, dui purus auctor tellus, et interdum..</p>
  <a class="btn btn-red">Learn More</a>
</article>
<article class="abs step" style="left:436px">
  <h3>Quick Start Guide</h3>
  <div class="icon"><svg width="70" height="56" viewBox="0 0 70 56"><path d="M35 12C26 6 14 6 4 8v40c10-2 22-2 31 4 9-6 21-6 31-4V8c-10-2-22-2-31 4z" fill="none" stroke="#ec2228" stroke-width="4"/><line x1="35" y1="12" x2="35" y2="52" stroke="#ec2228" stroke-width="4"/><path d="M44 4v14l4-3 4 3V4z" fill="#ec2228"/></svg></div>
  <p>Aliquam molestie, mi et imperdiet euismod, dui purus auctor tellus, et interdum..</p>
  <a class="btn btn-red">Learn More</a>
</article>
<article class="abs step" style="left:796px">
  <h3>At Home Works</h3>
  <div class="icon"><svg width="76" height="40" viewBox="0 0 76 40"><rect x="0" y="14" width="6" height="12" rx="2" fill="#ec2228"/><rect x="8" y="4" width="12" height="32" rx="3" fill="#ec2228"/><rect x="20" y="16" width="36" height="8" fill="#ec2228"/><rect x="56" y="4" width="12" height="32" rx="3" fill="#ec2228"/><rect x="70" y="14" width="6" height="12" rx="2" fill="#ec2228"/></svg></div>
  <p>Aliquam molestie, mi et imperdiet euismod, dui purus auctor tellus, et interdum..</p>
  <a class="btn btn-red">Learn More</a>
</article>

<section class="why">
  <h2 class="abs section-title" style="top:1126px">Why Choose Brightwick Supper Kits</h2>
  <p class="abs">Aliquam molestie, mi et imperdiet euismod, dui purus auctor tellus, et interdum lacus lectus et ante. Sed accumsan sollicitudin sapien, sit amet adipiscing turpis gravida ac. In congue, neque ac lobortis volutpat, libero mauris varius mi, vitae suscipit ipsum ligula vitae risus. Duis aliquam nibh a dui iaculis viverra id a velit. Vivamus egestas risus in magna varius commodo. Sed semper viverra egestas. Etiam pretium porttitor lectus, vel ornare neque porta volutpat. Ut et scelerisque ante. Donec erat purus, faucibus vitae congue vel, porttitor nec lectus. Aenean a nibh eget turpis vehicula tempus ac sed massa. Vestibulum dolor nulla, ultrices ac tincidunt sed, laoreet non est. Suspendisse lobortis turpis in odio blandit ac interdum lorem euismod. Etiam risus massa, vulputate eu pellentesque et, consectetur a neque.</p>
  <a class="abs btn btn-orange why-btn">Read More</a>
</section>

<div class="abs band" style="top:1394px;height:128px;border-top:1px solid var(--line)"></div>
<h2 class="abs section-title" style="top:1427px">Our Recipes</h2>

<article class="abs recipe" style="left:73px;top:1486px">
  <div class="dish d1" role="img" aria-label="Bowl of green bean and tomato salad"></div>
  <h4>Fusce accumsan</h4>
  <p>Vivamus egestas risus in magna varius commodo. Sed semper viverra egestas. Etiam pretium porttitor lectus vel ornare neque isus in magna varius commodo....</p>
  <a class="btn btn-orange more">Read More</a><a class="btn btn-red join">Join Now</a>
</article>
<article class="abs recipe" style="left:614px;top:1486px">
  <div class="dish d2" role="img" aria-label="Plate of mango and greens salad"></div>
  <h4>Fusce accumsan</h4>
  <p>Vivamus egestas risus in magna varius commodo. Sed semper viverra egestas. Etiam pretium porttitor lectus vel ornare neque isus in magna varius commodo....</p>
  <a class="btn btn-orange more">Read More</a><a class="btn btn-red join">Join Now</a>
</article>
<article class="abs recipe" style="left:73px;top:1718px">
  <div class="dish d3" role="img" aria-label="Bowl of chicken salad with tomatoes"></div>
  <h4>Fusce accumsan</h4>
  <p>Vivamus egestas risus in magna varius commodo. Sed semper viverra egestas. Etiam pretium porttitor lectus vel ornare neque isus in magna varius commodo....</p>
  <a class="btn btn-orange more">Read More</a><a class="btn btn-red join">Join Now</a>
</article>
<article class="abs recipe" style="left:614px;top:1718px">
  <div class="dish d4" role="img" aria-label="Plate of roasted vegetables with feta"></div>
  <h4>Fusce accumsan</h4>
  <p>Vivamus egestas risus in magna varius commodo. Sed semper viverra egestas. Etiam pretium porttitor lectus vel ornare neque isus in magna varius commodo....</p>
  <a class="btn btn-orange more">Read More</a><a class="btn btn-red join">Join Now</a>
</article>

<div class="abs band" style="top:1955px;height:119px;border-top:1px solid var(--line)"></div>
<h2 class="abs section-title" style="top:1982px">Our Expert Team</h2>

<article class="abs expert left" style="top:2042px">
  <div class="portrait" role="img" aria-label="Portrait of the nutrition therapist"></div>
  <h4>Tessa Marlow</h4>
  <div class="role">Nutrition Therapist</div>
  <p>Duis aliquam nibh a dui iaculis viverra id a velit. Vivamus egestas risus in magna varius commodo. Sed semper viverra egestas. Etiam pretium porttitor lectus, vel ornare neque porta volutpat. Ut et scelerisque ante. Donec erat purus, faucibus vitae congue vel, porttitor nec lectus. Aenean a nibh eget turpis vehicula tempus ac sed massa.</p>
</article>
<article class="abs expert right" style="top:2220px">
  <div class="portrait" role="img" aria-label="Portrait of the nutrition therapist"></div>
  <h4>Owen Carrick</h4>
  <div class="role">Nutrition Therapist</div>
  <p>Duis aliquam nibh a dui iaculis viverra id a velit. Vivamus egestas risus in magna varius commodo. Sed semper viverra egestas. Etiam pretium porttitor lectus, vel ornare neque porta volutpat. Ut et scelerisque ante. Donec erat purus, faucibus vitae congue vel, porttitor nec lectus. Aenean a nibh eget turpis vehicula tempus ac sed massa.</p>
</article>

<footer class="abs footer wood">
  <h5 style="left:73px">About Us</h5>
  <p class="about">Aliquam molestie, mi et imperdiet euismod, dui purus auctor tellus, et interdum lacus lectus et ante. Sed accumsan sollicitudin sapien sit amet adipiscing turpis gravida ac.</p>
  <h5 style="left:411px">Quick Links</h5>
  <ul class="links" style="left:411px"><li>Home</li><li>About Us</li><li>Recipes</li><li>How it Works</li><li>Meal Plans</li></ul>
  <ul class="links" style="left:511px"><li>Resources</li><li>Our Experts</li><li>Success Stories</li><li>Contact Us</li></ul>
  <h5 style="left:650px">Follow Us:</h5>
  <div class="social"><span></span><span></span><span></span><span></span><span></span></div>
  <h5 style="left:885px">Get a Free Meal Plan!</h5>
  <div class="field" style="top:60px">Name</div>
  <div class="field" style="top:101px">Email Address</div>
  <a class="btn btn-red submit">Submit</a>
</footer>
<div class="abs copy">Copyright © 2014. Brightwick Supper Kits. All Right Reserved</div>

</body>
</html>
```